New tech executive consulting company needs professionally branded document templates

We are a new business selling fractional board advisory and go-to-market consulting services into the Technology space. Tessaly Brink are experts in providing high-quality executive-level leaders on a part-time basis to tech companies in need of their expertise. We work closely with clients to understand their business needs, challenges, and goals, and provides customised solutions to help them succeed. Due to our audience we need the design to have a high quality, executive look and feel.

Our first website is live and can be found at tessalybrink.example. We also already have a logo which I've uploaded. Our brand is clean and uses orange to give it colour and an identity that stands out.

We need some document master templates created so we can create our own presentations (Google Slides & Powerpoint), PDF documents, and Word templates, and ideally also a LinkedIn banner.

```html
<!DOCTYPE html>
<html lang="en">
<head>
<meta charset="utf-8">
<title>Tessaly Brink – Presentation Template</title>
<link rel="stylesheet" href="https://fonts.googleapis.com/css2?family=Lato:wght@400;700;900&display=swap">
<style>
  :root {
    --navy: #2b3440;
    --navy-deep: #232b36;
    --slate: #3b4654;
    --orange: #e8834e;
    --peach: #f3d6c6;
    --ink: #2e2e2e;
    --white: #ffffff;
    --page: #ffffff;
  }
  * { box-sizing: border-box; margin: 0; padding: 0; }
  html, body {
    width: 1200px; height: 4147px; overflow: hidden;
    background: var(--page);
    font-family: "Lato", Arial, sans-serif;
    color: var(--ink);
  }
  .slide {
    position: absolute; left: 44px; width: 1112px; height: 625px;
    background: var(--white);
    box-shadow: 0 2px 8px rgba(0,0,0,0.18);
    overflow: hidden;
  }
  .slide--dark {
    background: linear-gradient(160deg, #4a5462 0%, #37414e 55%, #2c3541 100%);
    color: var(--white);
  }
  .slide-title {
    position: absolute; left: 30px; top: 26px;
    font-size: 56px; font-weight: 700; color: var(--navy); letter-spacing: 0.5px;
  }
  .brand-mark {
    position: absolute; right: 30px; top: 36px;
    font-weight: 900; font-size: 19px; line-height: 21px; letter-spacing: 2px;
    color: var(--navy); text-align: right;
  }
  .brand-mark--light { color: var(--white); }
  .footer-band {
    position: absolute; left: 0; bottom: 0; width: 100%; height: 29px;
  }
  .footer-band svg { position: absolute; inset: 0; }
  .footer-copy {
    position: absolute; left: 30px; top: 7px;
    font-size: 12px; color: var(--white);
  }
  .footer-page {
    position: absolute; right: 30px; top: 7px;
    font-size: 13px; color: var(--white);
  }

  /* cover */
  .cover-brand {
    position: absolute; left: 0; width: 100%; text-align: center;
    font-weight: 900; color: var(--white); letter-spacing: 8px;
  }
  .cover-tagline {
    position: absolute; left: 0; top: 405px; width: 100%; text-align: center;
    font-size: 42px; font-weight: 700; line-height: 54px; color: var(--white);
  }
  .cover-rule {
    position: absolute; left: 476px; top: 529px; width: 160px; height: 4px;
    background: var(--orange);
  }

  /* agenda */
  .agenda-list { position: absolute; left: 44px; top: 168px; list-style: none; }
  .agenda-list li {
    display: flex; align-items: center; height: 56px;
    font-size: 22px; font-weight: 700; color: var(--navy);
  }
  .agenda-list svg { width: 22px; height: 22px; margin-right: 26px; }

  /* photo placeholders */
  .photo {
    position: absolute;
    background: linear-gradient(135deg, #8b95a3 0%, #c9ced6 45%, #5a6473 100%);
  }

  /* about */
  .lead {
    position: absolute; left: 30px; top: 132px;
    font-size: 28px; font-weight: 700; color: var(--orange);
  }
  .body-copy { position: absolute; width: 560px; font-size: 19px; line-height: 32px; }
  .body-copy p + p { margin-top: 11px; }

  /* why choose */
  .feature {
    position: absolute; top: 186px; width: 300px; text-align: center;
  }
  .feature svg { width: 120px; height: 120px; display: block; margin: 0 auto; }
  .feature h3 {
    margin-top: 26px; font-size: 17px; font-weight: 700; color: var(--ink);
  }
  .feature p { margin-top: 8px; font-size: 14px; line-height: 26px; color: var(--ink); }

  /* thank you */
  .thanks {
    position: absolute; left: 0; top: 340px; width: 100%; text-align: center;
    font-size: 62px; font-weight: 700; color: var(--white);
  }
  .contact {
    position: absolute; top: 445px; width: 300px; text-align: center;
    font-size: 16px; color: var(--white);
  }
  .contact svg { width: 36px; height: 36px; display: block; margin: 0 auto 14px; }
</style>
</head>
<body>

<!-- Cover -->
<section class="slide slide--dark" style="top:55px">
  <div class="cover-brand" style="top:120px;font-size:104px;line-height:110px">TESSALY</div>
  <div class="cover-brand" style="top:232px;font-size:86px;line-height:92px">BRINK</div>
  <p class="cover-tagline">Experts in providing executive leadership<br>on demand</p>
  <div class="cover-rule"></div>
</section>

<!-- Agenda -->
<section class="slide" style="top:734px">
  <svg width="1112" height="596" style="position:absolute;left:0;top:0">
    <polygon points="733,0 1112,0 1112,596 343,596" fill="var(--navy)"/>
  </svg>
  <div class="photo" role="img" aria-label="Photo of a business team gathered around a meeting table"
       style="left:0;top:0;width:1112px;height:596px;clip-path:polygon(778px 0,1112px 0,1112px 596px,391px 596px)"></div>
  <h2 class="slide-title">AGENDA</h2>
  <div class="brand-mark brand-mark--light">TESSALY<br>BRINK</div>
  <ul class="agenda-list">
    <li><svg viewBox="0 0 22 22"><circle cx="11" cy="11" r="8.5" fill="none" stroke="var(--orange)" stroke-width="2"/><path d="M7 11.2l2.8 2.8L15 8.6" fill="none" stroke="var(--orange)" stroke-width="2"/></svg>Summary</li>
    <li><svg viewBox="0 0 22 22"><circle cx="11" cy="11" r="8.5" fill="none" stroke="var(--orange)" stroke-width="2"/><path d="M7 11.2l2.8 2.8L15 8.6" fill="none" stroke="var(--orange)" stroke-width="2"/></svg>About Us</li>
    <li><svg viewBox="0 0 22 22"><circle cx="11" cy="11" r="8.5" fill="none" stroke="var(--orange)" stroke-width="2"/><path d="M7 11.2l2.8 2.8L15 8.6" fill="none" stroke="var(--orange)" stroke-width="2"/></svg>Our Services</li>
    <li><svg viewBox="0 0 22 22"><circle cx="11" cy="11" r="8.5" fill="none" stroke="var(--orange)" stroke-width="2"/><path d="M7 11.2l2.8 2.8L15 8.6" fill="none" stroke="var(--orange)" stroke-width="2"/></svg>Why Choose Us</li>
    <li><svg viewBox="0 0 22 22"><circle cx="11" cy="11" r="8.5" fill="none" stroke="var(--orange)" stroke-width="2"/><path d="M7 11.2l2.8 2.8L15 8.6" fill="none" stroke="var(--orange)" stroke-width="2"/></svg>Testimonials</li>
    <li><svg viewBox="0 0 22 22"><circle cx="11" cy="11" r="8.5" fill="none" stroke="var(--orange)" stroke-width="2"/><path d="M7 11.2l2.8 2.8L15 8.6" fill="none" stroke="var(--orange)" stroke-width="2"/></svg>Thank You</li>
  </ul>
  <div class="footer-band">
    <svg width="1112" height="29"><rect width="1112" height="29" fill="var(--orange)"/><polygon points="988,0 1112,0 1112,29 958,29" fill="var(--navy)"/></svg>
    <span class="footer-copy">©Tessaly Brink. All Rights Reserved</span>
    <span class="footer-page">02</span>
  </div>
</section>

<!-- About us -->
<section class="slide" style="top:1413px">
  <h2 class="slide-title">ABOUT US</h2>
  <div class="brand-mark">TESSALY<br>BRINK</div>
  <p class="lead">The smart way to scale your business</p>
  <div class="body-copy" style="left:30px;top:198px">
    <p>Tessaly Brink are experts in providing high-quality executive-level leaders on a part-time basis to tech companies in need of their expertise. We work closely with clients to understand their business needs, challenges, and goals, and provides customised solutions to help them succeed.</p>
    <p>Our strategic insights, leadership, and collaborative approach make us a valuable partner for companies looking to drive growth and innovation. We are passionate about helping companies achieve their goals and are committed to providing the highest level of service to our clients.</p>
  </div>
  <div class="photo" role="img" aria-label="Photo of two colleagues reviewing a tablet in an office" style="left:688px;top:111px;width:396px;height:414px"></div>
  <svg width="1112" height="596" style="position:absolute;left:0;top:0;pointer-events:none">
    <line x1="667" y1="217" x2="752" y2="101" stroke="var(--orange)" stroke-width="4"/>
  </svg>
  <div class="footer-band">
    <svg width="1112" height="29"><rect width="1112" height="29" fill="var(--orange)"/><polygon points="988,0 1112,0 1112,29 958,29" fill="var(--navy)"/></svg>
    <span class="footer-copy">©Tessaly Brink. All Rights Reserved</span>
    <span class="footer-page">03</span>
  </div>
</section>

<!-- Profile -->
<section class="slide" style="top:2093px">
  <h2 class="slide-title">MARCUS HALE</h2>
  <div class="brand-mark">TESSALY<br>BRINK</div>
  <div class="photo" role="img" aria-label="Portrait photo of the founder" style="left:32px;top:129px;width:396px;height:414px;background:linear-gradient(135deg,#8a5a3c 0%,#c49a7a 40%,#2f4a78 100%)"></div>
  <svg width="1112" height="596" style="position:absolute;left:0;top:0;pointer-events:none">
    <line x1="362" y1="551" x2="448" y2="435" stroke="var(--orange)" stroke-width="4"/>
  </svg>
  <div class="body-copy" style="left:512px;top:197px">
    <p>Marcus Hale is a highly accomplished business leader with extensive experience in executive-level leadership and strategy. As the founder of Tessaly Brink, Marcus brings his years of experience in the technology industry to help companies achieve their goals.</p>
    <p>Throughout his career, Marcus has held executive positions in companies ranging from startups to large corporations. He has a deep understanding of the tech industry and has helped companies at all stages of maturity drive significant growth and innovation.</p>
  </div>
  <div class="footer-band">
    <svg width="1112" height="29"><rect width="1112" height="29" fill="var(--orange)"/><polygon points="988,0 1112,0 1112,29 958,29" fill="var(--navy)"/></svg>
    <span class="footer-copy">©Tessaly Brink. All Rights Reserved</span>
    <span class="footer-page">04</span>
  </div>
</section>

<!-- Why choose us -->
<section class="slide" style="top:2771px">
  <h2 class="slide-title">WHY CHOOSE US</h2>
  <div class="brand-mark">TESSALY<br>BRINK</div>
  <svg width="0" height="0" style="position:absolute">
    <defs>
      <linearGradient id="badge" x1="0" y1="0" x2="0" y2="1">
        <stop offset="0" stop-color="#e8834e"/><stop offset="1" stop-color="#3a3f4a"/>
      </linearGradient>
    </defs>
  </svg>
  <div class="feature" style="left:24px">
    <svg viewBox="0 0 120 120"><circle cx="60" cy="60" r="58" fill="var(--peach)"/><circle cx="60" cy="60" r="49" fill="url(#badge)"/>
      <g fill="none" stroke="#fff" stroke-width="2.5"><circle cx="60" cy="48" r="10"/><path d="M40 82c2-12 10-18 20-18s18 6 20 18"/><rect x="36" y="30" width="48" height="56" rx="4" opacity="0"/></g></svg>
    <h3>LOREM IPSUM</h3>
    <p>Lorem ipsum dolor sit amet, consectetur adipi scing elit, sed do eiusmod tempor incididunt ut labore et dolore magna aliqua. Quis ipsum sus­pendisse ultrices gravida.</p>
  </div>
  <div class="feature" style="left:404px">
    <svg viewBox="0 0 120 120"><circle cx="60" cy="60" r="58" fill="var(--peach)"/><circle cx="60" cy="60" r="49" fill="url(#badge)"/>
      <g fill="none" stroke="#fff" stroke-width="2.5"><circle cx="52" cy="66" r="9"/><circle cx="52" cy="66" r="16" stroke-dasharray="5 4"/><circle cx="74" cy="46" r="6"/><circle cx="74" cy="46" r="11" stroke-dasharray="4 3"/></g></svg>
    <h3>LOREM IPSUM</h3>
    <p>Lorem ipsum dolor sit amet, consectetur adipi scing elit, sed do eiusmod tempor incididunt ut labore et dolore magna aliqua. Quis ipsum sus­pendisse ultrices gravida.</p>
  </div>
  <div class="feature" style="left:784px">
    <svg viewBox="0 0 120 120"><circle cx="60" cy="60" r="58" fill="var(--peach)"/><circle cx="60" cy="60" r="49" fill="url(#badge)"/>
      <g fill="none" stroke="#fff" stroke-width="2.5"><circle cx="46" cy="48" r="8"/><circle cx="74" cy="48" r="8"/><path d="M32 78c2-10 7-14 14-14s12 4 14 14M60 78c2-10 7-14 14-14s12 4 14 14"/></g></svg>
    <h3>LOREM IPSUM</h3>
    <p>Lorem ipsum dolor sit amet, consectetur adipi scing elit, sed do eiusmod tempor incididunt ut labore et dolore magna aliqua. Quis ipsum sus­pendisse ultrices gravida.</p>
  </div>
  <div class="footer-band">
    <svg width="1112" height="29"><rect width="1112" height="29" fill="var(--orange)"/><polygon points="988,0 1112,0 1112,29 958,29" fill="var(--navy)"/></svg>
    <span class="footer-copy">©Tessaly Brink. All Rights Reserved</span>
    <span class="footer-page">05</span>
  </div>
</section>

<!-- Thank you -->
<section class="slide slide--dark" style="top:3451px">
  <div class="cover-brand" style="top:92px;font-size:80px;line-height:86px">TESSALY</div>
  <div class="cover-brand" style="top:182px;font-size:66px;line-height:72px">BRINK</div>
  <p class="thanks">THANK YOU</p>
  <div class="contact" style="left:106px">
    <svg viewBox="0 0 36 36"><circle cx="18" cy="18" r="17" fill="var(--orange)"/><path d="M12 10l4 1 1 4-2 1.5a11 11 0 0 0 5 5l1.5-2 4 1 1 4c-1 1.5-3 2-4.5 1.5A17 17 0 0 1 11 14.5C10.5 13 11 11 12 10z" fill="#fff"/></svg>
    +44 7700 900123
  </div>
  <div class="contact" style="left:403px;top:440px">
    <svg viewBox="0 0 36 36"><circle cx="18" cy="18" r="17" fill="var(--orange)"/><path d="M18 8a7 7 0 0 0-7 7c0 5 7 13 7 13s7-8 7-13a7 7 0 0 0-7-7z" fill="#fff"/><circle cx="18" cy="15" r="2.6" fill="var(--orange)"/></svg>
    Tessaly Brink, Address comes here
  </div>
  <div class="contact" style="left:701px;top:440px">
    <svg viewBox="0 0 36 36"><circle cx="18" cy="18" r="17" fill="var(--orange)"/><rect x="10" y="12" width="16" height="12" rx="1.5" fill="#fff"/><path d="M10.5 12.8L18 19l7.5-6.2" fill="none" stroke="var(--orange)" stroke-width="1.6"/></svg>
    info@tessalybrink.example
  </div>
</section>

</body>
</html>
```